Verpackungen Geschenkbox
Eine völlig unkomplizierte und tolle Zusammenarbeit. Und ein ganz tolles Ergebnis. Vielen Dank auch hier noch einmal : )
Zielgruppe
In unserem Studio können Kunden Keramik bemalen
Aufgabenstellung
Ich hätte gerne eine Vorlage für einen Aufkleber, den ich auf eine Verschenkbox machen kann. Diese Geschenkbox werde ich mit einer Rohkeramik füllen, zusätzlich alle Materialien die dafür benötigt werden, wie z.B. Glasuren, Pinsel etc. Diese Boxen sind fertig gerichtet, können direkt gekauft werden und die bemalte Keramik uns wieder zum Brennen gebracht werden. Der Aufkleber dazu soll zu unserem ganzen Stil passen und es soll unser Logo enthalten sein. Es soll zum Kaufen annimieren, aber nicht übertrieben sein. Eher klar auch in den Farben.
Der Aufkleber sollte max. 10 cm groß sein. Der Karton ist viereckig, unterschiedlich groß, so dass eine Tasse, Müslischale oder Teller reinpasst, mit ein paar kleine Fabdosen, Pinsel und anderes Materialien wie Schwamm oder Punktewerkzeug. Achtung, es ist keine Töpferei

```html
<!DOCTYPE html>
<html lang="de">
<head>
<meta charset="utf-8">
<title>Keramik Malset – Aufkleber</title>
<link rel="stylesheet" href="https://fonts.googleapis.com/css2?family=Playfair+Display:wght@700&family=Montserrat:wght@400;500&display=swap">
<style>
  :root {
    --paper: #fcfcfc;
    --sticker: #ffffff;
    --teal-dark: #1f6b70;
    --teal: #177a82;
    --teal-soft: #4c9ea8;
    --rule: #4d8e93;
    --edge: #e3e3e3;
    --disc: #e6e7e9;
    --disc-edge: #cfd0d2;
  }
  html, body {
    margin: 0;
    padding: 0;
    width: 1200px;
    height: 800px;
    overflow: hidden;
    background: var(--paper);
  }
  .canvas {
    position: relative;
    width: 1200px;
    height: 800px;
  }
  .sticker-art {
    position: absolute;
    inset: 0;
  }
  .brand-name {
    position: absolute;
    left: 162px;
    top: 420px;
    width: 500px;
    margin: 0;
    font-family: "Playfair Display", Georgia, serif;
    font-weight: 700;
    font-size: 52px;
    letter-spacing: 3px;
    color: var(--teal);
    line-height: 1;
  }
  .product-title {
    position: absolute;
    left: 572px;
    top: 262px;
    width: 376px;
    margin: 0;
    text-align: center;
    font-family: "Playfair Display", Georgia, serif;
    font-weight: 700;
    color: var(--teal-dark);
    line-height: 1;
  }
  .product-title .title-main {
    display: block;
    font-size: 66px;
    letter-spacing: 7px;
  }
  .product-title .title-sub {
    display: block;
    margin-top: -3px;
    font-size: 54px;
    letter-spacing: 6px;
  }
  .tagline {
    position: absolute;
    left: 573px;
    top: 471px;
    margin: 0;
    font-family: "Montserrat", Arial, sans-serif;
    color: var(--teal-dark);
    line-height: 1;
  }
  .tagline .tagline-lead {
    display: block;
    font-size: 30px;
    font-weight: 400;
    letter-spacing: 3.4px;
  }
  .tagline .tagline-contents {
    display: block;
    margin-top: 10px;
    font-size: 20.5px;
    font-weight: 500;
    letter-spacing: 2.6px;
  }
</style>
</head>
<body>
<main class="canvas">
  <svg class="sticker-art" width="1200" height="800" viewBox="0 0 1200 800">
    <rect class="sticker-body" x="127" y="124" width="937" height="524" rx="48" fill="var(--sticker)" stroke="var(--edge)" stroke-width="2.5"/>

    <g class="frame" fill="none" stroke="var(--teal-dark)">
      <rect x="188" y="143.5" width="818" height="5" rx="2" stroke-width="2.2"/>
      <rect x="188" y="623" width="818" height="5" rx="2" stroke-width="2.2"/>
      <rect x="144.5" y="184" width="5" height="406" rx="2" stroke-width="2.2"/>
      <rect x="1041.5" y="184" width="5" height="406" rx="2" stroke-width="2.2"/>
    </g>

    <g class="corner-flourishes" fill="var(--teal-dark)">
      <rect role="img" aria-label="Ornament Ecke oben links" x="152" y="148" width="34" height="34" rx="12"/>
      <rect role="img" aria-label="Ornament Ecke oben rechts" x="1006" y="148" width="34" height="34" rx="12"/>
      <rect role="img" aria-label="Ornament Ecke unten links" x="152" y="590" width="34" height="34" rx="12"/>
      <rect role="img" aria-label="Ornament Ecke unten rechts" x="1006" y="590" width="34" height="34" rx="12"/>
    </g>

    <circle class="brand-disc" cx="364" cy="389" r="127" fill="var(--disc)" stroke="var(--disc-edge)" stroke-width="2"/>

    <g class="title-rules" stroke="var(--rule)" stroke-width="2">
      <line x1="566" y1="233" x2="704" y2="233"/>
      <line x1="791" y1="233" x2="926" y2="233"/>
      <line x1="566" y1="545" x2="926" y2="545"/>
    </g>

    <rect class="bow-placeholder" role="img" aria-label="Schleife als Zierelement" x="708" y="212" width="80" height="38" rx="6" fill="var(--teal-dark)"/>

    <rect class="bowl-placeholder" role="img" aria-label="Abbildung einer türkisfarbenen Keramikschale" x="703" y="400" width="98" height="61" rx="6" fill="var(--teal-soft)"/>
  </svg>

  <p class="brand-name">TONFREUDE</p>

  <h1 class="product-title">
    <span class="title-main">KERAMIK</span>
    <span class="title-sub">MALSET</span>
  </h1>

  <p class="tagline">
    <span class="tagline-lead">Alles was du bruchst-</span>
    <span class="tagline-contents">Keramil, Farben, Pinsel &amp; mehr</span>
  </p>
</main>
</body>
</html>
```